Looking for Web Design for NFT project

We are an animal charity company and we are looking for a web designer for our latest NFT project. We need a custom designed single page web site structured in a specific way: about us section, how to buy our nft explanation, roadmap etc. It is strongly required the theme of the website to emphasize the Chinese culture. We insist on this since the animals on the NFTs have chinese descent.

Here are good examples of similar websites in terms of how the web page should be structured:

https://quillfernharbor.com/#/home
https://wobblets.io/
https://tarvelinplay.com/
https://mossgarland.rip/

The structure of our website should be similar to the websites listed above, however, the theme the web page should be original, more playful than serious, colourful, it should be fun and in chinese thematic. The NFTs will be 100x100 pixel 16bit animals.

Target markets: Cryptocurrency and NFT collectors/creators

Target Market(s)

Cryptocurrency and NFT collectors/creators

Industry/Entity Type

NFT Space

Coding

Coded - Design and coding required

Number of Pages Required

1 page

Requirements
Must have
• Chinese thematics / Pekingese dog breed oriented
Nice to have
• The NFTs will be 100x100 pixel pekingese dogs
Should not have
• Anything that is directly related to crypto

```html
<!DOCTYPE html>
<html lang="en">
<head>
<meta charset="utf-8">
<title>Lantern Paws — NFT Collection</title>
<link href="https://fonts.googleapis.com/css2?family=Fredoka:wght@500;600;700&family=Rajdhani:wght@500;600;700&display=swap" rel="stylesheet">
<style>
:root{
  --bg:#f6eafb;
  --bg-hero:#f8e7f3;
  --pattern-a:#f6e2ee;
  --pattern-b:#f1dcea;
  --navy:#1b1a3e;
  --teal:#2fd1c4;
  --red:#f2523a;
  --ghost:#d7d4d9;
  --text:#3a3550;
  --rule:#2a2838;
  --road-a:#e2d9e6;
  --road-b:#cfc6d4;
  --knot:#8e8a93;
  --orange:#e8671a;
  --purple:#7a2484;
  --blue:#1d6fc2;
  --green:#5c9a12;
  --white:#ffffff;
}
*{box-sizing:border-box;margin:0;padding:0}
html,body{width:1200px;height:4979px;overflow:hidden;background:var(--bg)}
body{font-family:"Rajdhani",sans-serif;color:var(--text)}
.page{position:relative;width:1200px;height:4979px;overflow:hidden;background:var(--bg)}
.abs{position:absolute}
.pattern-area{position:absolute;left:0;width:1200px;background:linear-gradient(135deg,var(--pattern-a),var(--pattern-b) 50%,var(--pattern-a))}
.knot{position:absolute;width:70px;height:70px;border-radius:12px;background:radial-gradient(circle,var(--knot) 20%,rgba(142,138,147,.35) 70%,transparent 100%)}
.art{position:absolute;border-radius:12px}
.brand-art{left:185px;top:24px;width:124px;height:82px;background:linear-gradient(180deg,#ece3f0,#d9cfd6);border-radius:10px}
.brand-name{left:141px;top:104px;font-family:"Rajdhani",sans-serif;font-weight:600;font-size:33px;color:var(--navy);letter-spacing:.5px;white-space:nowrap}
.socials{left:734px;top:36px;display:flex;gap:16px}
.dot{width:15px;height:15px;border-radius:50%;background:var(--navy)}
.btn{display:flex;align-items:center;justify-content:center;border-radius:30px;font-family:"Rajdhani",sans-serif;font-weight:700;font-size:16px;letter-spacing:.5px;color:var(--white);background:var(--red)}
.btn-outline{background:transparent;color:var(--red);border:2px solid var(--red)}
.nav{left:485px;top:101px;font-weight:600;font-size:14px;color:var(--navy)}
.nav span{position:absolute;white-space:nowrap}
.nav .active{border-bottom:2px solid var(--red);padding-bottom:4px;color:var(--navy)}
.hero-title{left:141px;top:212px;font-family:"Fredoka",sans-serif;font-weight:700;font-size:64px;line-height:70px;color:var(--navy);white-space:nowrap}
.hero-title .accent{color:var(--teal)}
.hero-sub{left:141px;top:384px;width:500px;font-size:20px;line-height:29px;font-weight:600;color:var(--navy)}
.store{border-radius:6px;background:#111}
.ghost{left:-8px;font-family:"Fredoka",sans-serif;font-weight:700;font-size:232px;line-height:1;color:var(--ghost);white-space:nowrap;letter-spacing:4px}
.heading{font-family:"Fredoka",sans-serif;font-weight:700;font-size:60px;line-height:70px;color:var(--navy)}
.heading .accent{color:var(--teal)}
.copy{font-size:14px;line-height:26.5px;font-weight:500;color:var(--text);text-align:justify}
.rule{left:0;width:1200px;height:3px;background:var(--rule)}
.road-art{left:130px;top:2520px;width:1050px;height:860px;border-radius:200px;background:radial-gradient(ellipse at 50% 50%,var(--road-b),var(--road-a) 60%,transparent 100%)}
.milestone{position:absolute;display:flex;flex-direction:column;align-items:center;justify-content:center;text-align:center;border-radius:50%;background:var(--white);font-family:"Rajdhani",sans-serif;color:var(--navy);border-style:solid;border-width:18px}
.milestone .big{font-weight:700;font-size:25px;line-height:30px}
.milestone .small{font-weight:700;font-size:13px;line-height:17px;margin-top:4px}
.faq-item{position:absolute;left:251px;width:700px;background:var(--white);border-radius:10px;box-shadow:0 3px 8px rgba(60,40,80,.12);display:flex;align-items:center;justify-content:space-between;padding:0 28px 0 70px;font-weight:700;font-size:17px;color:var(--navy)}
.faq-toggle{width:20px;height:20px;border-radius:50%;background:var(--navy);position:relative;flex:none}
.faq-toggle::before,.faq-toggle.plus::after{content:"";position:absolute;left:5px;top:9px;width:10px;height:2px;background:var(--white)}
.faq-toggle.plus::after{transform:rotate(90deg)}
.footer{left:0;top:4827px;width:1200px;height:152px;background:var(--bg)}
</style>
</head>
<body>
<div class="page">

  <!-- Header and hero -->
  <div class="pattern-area" style="top:0;height:725px" role="img" aria-label="Faint Chinese lattice pattern"></div>
  <div class="knot" style="left:555px;top:-20px" role="img" aria-label="Chinese knot ornament"></div>
  <div class="knot" style="left:585px;top:365px" role="img" aria-label="Chinese knot ornament"></div>
  <div class="art brand-art" role="img" aria-label="Pekingese dog head illustration"></div>
  <div class="abs brand-name">LANTERN PAWS</div>
  <div class="abs socials"><div class="dot"></div><div class="dot"></div><div class="dot"></div><div class="dot"></div></div>
  <div class="abs btn" style="left:881px;top:17px;width:174px;height:53px">JOIN NOW</div>
  <nav class="abs nav">
    <span class="active" style="left:0">HOME</span>
    <span style="left:73px">ABOUT US</span>
    <span style="left:173px">HOW TO BUY OUR NFT EXPLANATION</span>
    <span style="left:441px">ROADMAP</span>
  </nav>
  <svg class="abs" style="left:1034px;top:99px" width="20" height="20" viewBox="0 0 20 20"><circle cx="8" cy="8" r="6" fill="none" stroke="var(--teal)" stroke-width="2.5"/><line x1="12.5" y1="12.5" x2="18" y2="18" stroke="var(--teal)" stroke-width="2.5"/></svg>

  <h1 class="abs hero-title">NFT COLLECTION<br><span class="accent">BY LANTERN PAWS</span></h1>
  <p class="abs hero-sub">Sed ut perspiciatis unde omnis iste natus error sit voluptatem accusantium doludantium</p>
  <div class="abs btn" style="left:143px;top:483px;width:172px;height:54px">JOIN NOW</div>
  <div class="abs btn btn-outline" style="left:328px;top:483px;width:169px;height:54px">WATCH VIDEO</div>
  <div class="abs store" style="left:143px;top:578px;width:172px;height:54px"></div>
  <div class="abs store" style="left:325px;top:578px;width:175px;height:54px"></div>
  <div class="art" style="left:719px;top:140px;width:417px;height:556px;background:linear-gradient(180deg,#a07a52,#7a5a3c 55%,#c9bfc4 100%);border-radius:40px" role="img" aria-label="Illustrated Pekingese dog sitting"></div>

  <!-- About -->
  <div class="abs ghost" style="top:716px">ABOUT US</div>
  <h2 class="abs heading" style="left:558px;top:886px">ABOUT <span class="accent">US</span></h2>
  <div class="abs copy" style="left:558px;top:980px;width:497px">
    <p>Lorem ipsum dolor sit amet, consectetur adipiscing elit, sed do eiusmod tempor incididunt ut labore et dolore magna aliqua. Quis ipsum suspendisse ultrices gravida. Risus commodo viverra maecenas accumsan lacus vel facilisis. Lorem ipsum dolor sit amet, consectetur adipiscing elit, sed do eiusmod tempor incididunt ut labore et dolore magna aliqua. Quis ipsum suspendisse ultrices gravida. Risus commodo viverra maecenas accumsan</p>
    <p style="margin-top:26px">Lacus vel facilisis. Lorem ipsum dolor sit amet, consectetur adipiscing elit, sed do eiusmod tempor incididunt ut labore et dolore magna aliqua. Quis ipsum suspendisse ultrices gravida. Risus commodo viverra maecenas accumsan lacus vel faciverra maecenas accumsaniverra maecenas accumsanilisis.</p>
  </div>
  <div class="abs btn" style="left:558px;top:1310px;width:172px;height:54px">JOIN NOW</div>
  <div class="art" style="left:0;top:1059px;width:537px;height:409px;background:linear-gradient(135deg,#f3eef4,#ddd5df)" role="img" aria-label="Line drawing of a Chinese dragon"></div>
  <div class="art" style="left:1001px;top:1362px;width:158px;height:149px;background:linear-gradient(160deg,#6d4a34,#e9e1da)" role="img" aria-label="Small Shih Tzu puppy"></div>
  <div class="abs rule" style="top:1491px"></div>

  <!-- How to buy -->
  <h2 class="abs heading" style="left:0;top:1612px;width:1200px;text-align:center">HOW TO BUY OUR NFT<br><span class="accent">EXPLANATION</span></h2>
  <div class="abs copy" style="left:218px;top:1782px;width:764px;text-align:center">
    <p>Lorem ipsum dolor sit amet, consectetur adipiscing elit, sed do eiusmod tempor incididunt ut labore et dolore magna aliqua. Quis ipsum suspendisse ultrices gravida. Risus commodo viverra maecenas accumsan lacus vel facilisis. Lorem ipsum dolor sit amet, consectetur adipiscing elit, sed do eiusmod tempor incididunt ut labore et dolore magna aliqua. Quis ipsum suspendisse ultrices gravida. Risus commodo viverra maecenas accumsanLacus vel facilisis. Lorem ipsum dolor sit amet, consectetur adipiscing elit, sed do eiusmod tempor incididunt ut labore et dolore magna aliqua. Quis ipsum suspendisse ultrices gravida. Risus commodo viverra maecenas accumsan lacus vel faciverra maecenas accumsaniverra maecenas accumsanilisis.</p>
    <p style="margin-top:26px">Modo viverra maecenas accumsan lacus vel facilisis. Lorem ipsum dolor sit amet, consectetur adipiscing elit, sed do eiusmod tempor incididunt ut labore et dolore magna aliqua. Quis ipsum suspendisse ultrices gravida. Risus commodo viverra maecenas accumsanLacus vel facilisis. Lorem ipsum dolor sit amet, consectetur adipiscing elit, sed do eiusmod tempor incididunt ut labore et dolore magna aliqua. Quis ipsum suspendisse ultrices gravida.</p>
  </div>
  <div class="abs btn" style="left:514px;top:2112px;width:172px;height:54px">JOIN NOW</div>
  <div class="abs ghost" style="top:2222px">HOW TO B</div>
  <div class="art" style="left:100px;top:2328px;width:132px;height:170px;background:linear-gradient(180deg,#f1ede9,#d8d1cb)" role="img" aria-label="Sketch of a fluffy Chow Chow dog"></div>
  <div class="abs rule" style="top:2464px"></div>

  <!-- Roadmap -->
  <div class="abs road-art" role="img" aria-label="Illustration of a winding road linking the milestones"></div>
  <div class="milestone" style="left:204px;top:2662px;width:280px;height:280px;border-color:var(--orange)"><div class="big">DEVELOPING<br><span style="color:var(--orange)">NFT GAMS</span></div><div class="small">(Tarvelin 1 and Tarvelin<br>2) Q1 - Q4, 2020)</div></div>
  <div class="milestone" style="left:552px;top:2615px;width:256px;height:256px;border-color:var(--purple)"><div class="big">REACHING 1ST<br><span style="color:var(--purple)">PLACE IN WORD</span></div><div class="small">Game category on the<br>Petal Market and Orchard<br>Store. Q1-Q2, 2021</div></div>
  <div class="milestone" style="left:493px;top:2956px;width:270px;height:270px;border-color:var(--blue)"><div class="big">REACHING 100<br><span style="color:var(--blue)">MILLION INSTALLS</span></div><div class="small">worldwide and 1st place in<br>NFT Games category<br>on the Petal Market.<br>Q3, 2021</div></div>
  <div class="milestone" style="left:846px;top:2925px;width:256px;height:256px;border-color:var(--green)"><div class="big">LAUNCH ON<br><span style="color:var(--green)">OCTOBER 1ST,</span><br>5PM UTC</div></div>
  <h2 class="abs heading" style="left:73px;top:3056px">ROAD<span class="accent">MAP</span></h2>
  <p class="abs copy" style="left:58px;top:3160px;width:338px;text-align:center">Lorem ipsum dolor sit amet, consectetur adipiscing elit, sed do eiusmod tempor incididunt ut labore et dolore magna aliqua. Quis ipsum suspendisse ultrices gravida. Risus commodo viverra maecenas accumsan lacus vel facilisis.</p>
  <div class="abs" style="left:146px;top:3378px;width:910px;height:512px;background:var(--white);box-shadow:0 2px 8px rgba(0,0,0,.15)"></div>
  <div class="abs" style="left:152px;top:3384px;width:898px;height:500px;background:linear-gradient(180deg,#5f8f2a 0%,#8aa63a 50%,#c2b43e 100%)" role="img" aria-label="Photo of a Pomeranian puppy running on grass"></div>
  <div class="abs ghost" style="top:3897px">ROADMAP</div>
  <div class="abs rule" style="top:4101px"></div>

  <!-- FAQ -->
  <div class="pattern-area" style="top:4104px;height:720px" role="img" aria-label="Faint Chinese lattice pattern"></div>
  <div class="knot" style="left:565px;top:4420px" role="img" aria-label="Chinese knot ornament"></div>
  <div class="knot" style="left:965px;top:4425px" role="img" aria-label="Chinese knot ornament"></div>
  <div class="art" style="left:19px;top:4115px;width:170px;height:116px;background:linear-gradient(180deg,#f4f0f2,#dcd4d8)" role="img" aria-label="Sketch of a long-haired dog"></div>
  <h2 class="abs heading" style="left:0;top:4186px;width:1200px;text-align:center">FAQ</h2>
  <div class="faq-item" style="top:4310px;height:72px">What is aliquip ex ea commodo consequat?<div class="faq-toggle"></div></div>
  <p class="abs copy" style="left:268px;top:4398px;width:676px;font-size:13.5px;line-height:24px">Lorem ipsum dolor sit amet, consectetur adipiscing elit, sed do eiusmod tempor incididunt ut labore et dolore magna ipsum suspendisse ultrices gravida. Risus commodo viverra maecenas accumsan lacus vel facilisis.</p>
  <div class="faq-item" style="top:4474px;height:66px">Which is sint occaecat cupidatat non proident?<div class="faq-toggle plus"></div></div>
  <div class="faq-item" style="top:4566px;height:64px">What is architecto beatae vitae dicta sunt explicabo?<div class="faq-toggle plus"></div></div>
  <div class="faq-item" style="top:4658px;height:64px">What is Duis aute irure dolor in reprehenderit?<div class="faq-toggle plus"></div></div>
  <div class="art" style="left:995px;top:4627px;width:187px;height:183px;background:radial-gradient(circle,#ffffff 30%,#d2ccd2 100%);border-radius:50%" role="img" aria-label="Line drawing of a Pekingese head"></div>

  <!-- Footer -->
  <div class="abs rule" style="top:4824px"></div>
  <footer class="abs footer">
    <div class="abs" style="left:149px;top:70px;font-weight:700;font-size:17px;color:var(--navy)">GET ON THE LIST</div>
    <div class="abs" style="left:321px;top:57px;width:206px;height:46px;background:var(--white);border:1px solid #d5cfda;font-size:12px;padding:14px 12px;color:#555">Enter Email</div>
    <div class="abs" style="left:527px;top:57px;width:101px;height:46px;background:var(--red);color:var(--white);font-weight:700;font-size:13px;display:flex;align-items:center;justify-content:center">SUBSCRIBE</div>
    <div class="abs" style="left:732px;top:58px;font-size:12px;font-weight:500;color:var(--navy);white-space:nowrap">© 2021 Lantern Paws.All Rights Reserved &nbsp;|&nbsp; Privacy &nbsp;|&nbsp; Terms</div>
    <div class="abs" style="left:732px;top:86px;display:flex;gap:12px"><div class="dot"></div><div class="dot"></div><div class="dot"></div></div>
  </footer>
</div>
</body>
</html>
```